Now Open Poster

We need a banner for our sports supplement and nutritional store, Vale Nutrition.
We were hoping for some sort of creative word art piece.
I have drawn my own mock up just to give you all a very basic starting point. But you are free to go with whatever you feel will work best.
The primary objective is simply to explain a little about what the company does, and then direct traffic towards the store with an 'Open Arrow' pointing left.
Text words we have chosen are:
Protein
Creatine
Health
Fitness
Sports Science
Nutrition
Energy
Achievement
Amino Acids
Organic
Supplements
Performance
Testosterone Support
Vitamins
Growth
Diet
Happiness
Weight Loss
Strong
Natural
Vitality
Accomplished
Below the word art we want our logo (See attached options)
Then below the logo the phrase "Success Starts Here"
Dimensions of the poster are 140cm x 60cm.
Colours: Blues/Whites/Greys/Blacks (Lots of white space please)
Here are some cool pieces I found that had some interesting elements that I liked (I'd love to see a mash-up of styles with a street art feel to it. Something funky!):
http://www.snipboard.com/pin/574018263940517382/
http://www.snipboard.com/pin/649205817364028195/
http://www.snipboard.com/pin/574018263948306271/
http://www.snipboard.com/pin/574018263946210859/
http://www.snipboard.com/pin/836140297512608364/
Thanks for reading, message me if you have any further questions!
- Liam
Store

```html
<!DOCTYPE html>
<html lang="en">
<head>
<meta charset="utf-8">
<title>Vale Nutrition – Now Open Banner</title>
<link rel="stylesheet" href="https://fonts.googleapis.com/css2?family=Alfa+Slab+One&family=Archivo+Black&family=Audiowide&family=Comfortaa:wght@300&family=Great+Vibes&family=Kalam:wght@400&family=Lato:wght@400;900&family=Lobster&family=Montserrat:wght@700&family=Oranienbaum&family=Oswald:wght@300;400;500&family=Quicksand:wght@300;400&family=Righteous&family=Roboto+Condensed:wght@400;700&family=Ultra&family=Yellowtail&family=Roboto+Slab:wght@900&display=swap">
<style>
  :root {
    --backdrop: #2b3440;
    --paper: #fdfbea;
    --open-red: #e8202a;
    --arrow-green: #3fa535;
    --arrow-light: #8fd14f;
    --blue-bright: #1b8fd2;
    --blue-mid: #2f78c0;
    --blue-deep: #0d3f8c;
    --blue-slate: #4f74b8;
    --blue-pale: #a9c4e6;
    --blue-sky: #6fc9f2;
    --blue-steel: #5a7fc0;
    --band-blue: #1777c2;
    --white: #ffffff;
  }
  * { margin: 0; padding: 0; box-sizing: border-box; }
  html, body { width: 1200px; height: 1200px; overflow: hidden; }
  body { background: var(--backdrop); position: relative; }

  .banner {
    position: absolute; left: 355px; top: 20px;
    width: 490px; height: 1160px;
    background: var(--paper);
    overflow: hidden;
  }
  .word-line {
    position: absolute; left: 0; width: 100%;
    text-align: center; line-height: 1; white-space: nowrap;
  }
  .word-line span { display: inline-block; }

  .open-sign { top: 22px; }
  .open-sign .open-word {
    font-family: "Roboto Slab", serif; font-weight: 900;
    font-size: 62px; color: var(--open-red); letter-spacing: 1px;
    margin-right: 30px;
  }
  .open-arrow { position: absolute; left: 240px; top: 36px; width: 110px; height: 82px; }

  .w-protein { font-family: "Lobster", cursive; color: var(--blue-bright); font-size: 54px; }
  .w-creatine { font-family: "Oswald", sans-serif; font-weight: 400; color: var(--blue-mid); font-size: 40px; }
  .w-health { font-family: "Righteous", sans-serif; font-style: italic; color: var(--blue-pale); font-size: 40px; letter-spacing: 3px; }
  .w-fitness { font-family: "Oswald", sans-serif; font-weight: 300; color: var(--blue-mid); font-size: 40px; }
  .w-sports { font-family: "Roboto Condensed", sans-serif; font-weight: 700; color: var(--blue-slate); font-size: 54px; }
  .w-nutrition { font-family: "Comfortaa", sans-serif; font-weight: 300; color: var(--blue-sky); font-size: 50px; }
  .w-energy { font-family: "Audiowide", sans-serif; color: var(--blue-mid); font-size: 42px; }
  .w-achievement { font-family: "Roboto Condensed", sans-serif; font-weight: 400; color: var(--blue-bright); font-size: 52px; }
  .w-amino { font-family: "Alfa Slab One", serif; color: var(--blue-deep); font-size: 24px; }
  .w-organic { font-family: "Montserrat", sans-serif; font-weight: 700; color: var(--blue-mid); font-size: 40px; letter-spacing: 10px; }
  .w-supplements { font-family: "Great Vibes", cursive; color: var(--blue-steel); font-size: 48px; letter-spacing: 5px; }
  .w-performance { font-family: "Oswald", sans-serif; font-weight: 300; color: var(--blue-slate); font-size: 58px; letter-spacing: 7px; }
  .w-testosterone { font-family: "Oranienbaum", serif; color: var(--blue-steel); font-size: 52px; letter-spacing: -1px; }
  .w-vitamins { font-family: "Archivo Black", sans-serif; color: var(--blue-deep); font-size: 36px; }
  .w-growth { font-family: "Quicksand", sans-serif; font-weight: 400; color: var(--blue-deep); font-size: 56px; }
  .w-diet { font-family: "Oswald", sans-serif; font-weight: 400; color: var(--blue-mid); font-size: 54px; }
  .w-happiness { font-family: "Lobster", cursive; color: var(--blue-bright); font-size: 50px; }
  .w-weight { font-family: "Quicksand", sans-serif; font-weight: 300; color: var(--blue-mid); font-size: 46px; }
  .w-strong { font-family: "Archivo Black", sans-serif; color: var(--blue-slate); font-size: 30px; }
  .w-natural { font-family: "Lato", sans-serif; font-weight: 400; color: var(--blue-deep); font-size: 38px; }
  .w-vitality { font-family: "Ultra", serif; color: var(--blue-steel); font-size: 44px; }
  .w-accomplished { font-family: "Kalam", cursive; color: var(--blue-deep); font-size: 46px; }

  .brand-band {
    position: absolute; left: 0; top: 971px; width: 100%; height: 82px;
    background: var(--band-blue);
  }
  .brand-name {
    position: absolute; left: 40px; top: 14px; width: 140px;
    font-family: "Lato", sans-serif; font-weight: 900; color: var(--white);
    font-size: 26px; line-height: 1.05; text-align: right;
  }
  .brand-mark {
    position: absolute; left: 188px; top: 961px;
    width: 114px; height: 114px; border-radius: 50%;
    background: var(--paper); border: 3px solid var(--band-blue);
    box-shadow: 0 0 0 3px var(--paper);
  }
  .tagline {
    position: absolute; left: 0; top: 1062px; width: 100%;
    text-align: center; font-family: "Yellowtail", cursive;
    font-size: 42px; color: var(--open-red);
    transform: rotate(-8deg); padding-right: 40px;
  }
</style>
</head>
<body>
  <main class="banner">
    <div class="word-line open-sign"><span class="open-word">OPEN</span></div>
    <svg class="open-arrow" viewBox="0 0 110 82" aria-label="Arrow pointing left">
      <defs>
        <linearGradient id="arrowFill" x1="0" y1="0" x2="0" y2="1">
          <stop offset="0" stop-color="var(--arrow-light)"/>
          <stop offset="1" stop-color="var(--arrow-green)"/>
        </linearGradient>
      </defs>
      <path d="M72 6 C96 10 104 36 86 52 C76 61 62 63 48 63 L48 78 L6 52 L48 26 L48 41 C62 41 74 39 80 32 C86 24 82 14 72 6 Z" fill="url(#arrowFill)"/>
    </svg>

    <div class="word-line" style="top:108px"><span class="w-protein">Protein,</span> <span class="w-creatine">Creatine,</span></div>
    <div class="word-line" style="top:162px"><span class="w-health">Health,</span> <span class="w-fitness">FITNESS,</span></div>
    <div class="word-line" style="top:206px"><span class="w-sports">Sports Science,</span></div>
    <div class="word-line" style="top:257px"><span class="w-nutrition">Nutrition,</span></div>
    <div class="word-line" style="top:304px"><span class="w-energy">ENERGY,</span></div>
    <div class="word-line" style="top:347px"><span class="w-achievement">Achievement,</span></div>
    <div class="word-line" style="top:392px"><span class="w-amino">Amino Acids,</span></div>
    <div class="word-line" style="top:419px"><span class="w-organic">Organic,</span></div>
    <div class="word-line" style="top:467px"><span class="w-supplements">Supplements,</span></div>
    <div class="word-line" style="top:516px"><span class="w-performance">PERFORMANCE,</span></div>
    <div class="word-line" style="top:573px"><span class="w-testosterone">Testosterone Support,</span></div>
    <div class="word-line" style="top:628px"><span class="w-vitamins">VITAMINS,</span></div>
    <div class="word-line" style="top:667px"><span class="w-growth">Growth,</span> <span class="w-diet">Diet,</span></div>
    <div class="word-line" style="top:722px"><span class="w-happiness">Happiness,</span></div>
    <div class="word-line" style="top:771px"><span class="w-weight">Weight Loss,</span></div>
    <div class="word-line" style="top:813px"><span class="w-strong">Strong,</span> <span class="w-natural">Natural,</span></div>
    <div class="word-line" style="top:851px"><span class="w-vitality">Vitality,</span></div>
    <div class="word-line" style="top:894px"><span class="w-accomplished">Accomplished,</span></div>

    <div class="brand-band">
      <div class="brand-name">Vale<br>Nutrition</div>
    </div>
    <div class="brand-mark"></div>

    <div class="tagline">Success Starts Here</div>
  </main>
</body>
</html>
```